Business Card Design Project

Business Card
We are rebranding with a new logo
Industry/Entity Type
Business
Contact Information for Business Card
Dennis Morvale +61 487215963 dennis@quorv.com.au P.O. Box 872 Fernlow QLD 4309
Requirements
Must have
- Logo

```html
<!DOCTYPE html>
<html lang="en">
<head>
<meta charset="utf-8">
<title>Quorv International – Business Card</title>
<link rel="stylesheet" href="https://fonts.googleapis.com/css2?family=Source+Sans+3:wght@400;600&display=swap">
<style>
  :root {
    --page-bg: #d9d6d1;
    --card-bg: #eeeeec;
    --navy: #1d4a78;
    --navy-deep: #163a60;
    --blue-light: #2f6aa6;
    --orange: #e0641e;
    --orange-deep: #c24f12;
    --ink: #2a2a2a;
    --name-grey: #d6dbe2;
    --brand-blue: #1f5f9e;
  }
  * { margin: 0; padding: 0; box-sizing: border-box; }
  html, body {
    width: 1200px; height: 969px; overflow: hidden;
    background: var(--page-bg);
    font-family: "Source Sans 3", Arial, sans-serif;
  }
  .business-card {
    position: absolute;
    left: 100px; top: 200px;
    width: 1000px; height: 569px;
    background: var(--card-bg);
    overflow: hidden;
    box-shadow: 0 10px 30px rgba(0,0,0,0.18);
  }
  .card-wave { position: absolute; inset: 0; width: 100%; height: 100%; }
  .holder-name {
    position: absolute; right: 48px; top: 58px;
    font-size: 29px; font-weight: 600; letter-spacing: 1px;
    color: var(--name-grey); text-transform: uppercase;
  }
  .brand-name {
    position: absolute; left: 62px; top: 228px;
    color: var(--brand-blue); font-weight: 600; line-height: 1;
    display: flex; align-items: center; gap: 20px;
  }
  .brand-mark {
    width: 26px; height: 26px; border-radius: 50%;
    background: var(--brand-blue);
  }
  .brand-text .primary { display: block; font-size: 104px; letter-spacing: -1px; }
  .brand-text .secondary { display: block; font-size: 38px; letter-spacing: 6px; margin-top: 6px; text-transform: uppercase; }
  .contact-list {
    position: absolute; left: 52px; top: 432px;
    list-style: none; font-size: 23px; color: var(--ink);
  }
  .contact-list li { display: flex; align-items: center; gap: 16px; height: 30px; }
  .contact-icon { width: 20px; height: 20px; fill: var(--navy); flex: none; }
  .postal-address {
    position: absolute; right: 48px; top: 460px;
    font-style: normal; text-align: right;
    font-size: 25px; line-height: 31px; color: var(--ink);
  }
</style>
</head>
<body>
  <div class="business-card">
    <svg class="card-wave" viewBox="0 0 1000 569" preserveAspectRatio="none" aria-hidden="true">
      <defs>
        <linearGradient id="bandBlue" x1="0" y1="0" x2="1" y2="0">
          <stop offset="0" stop-color="var(--navy-deep)"/>
          <stop offset="0.55" stop-color="var(--blue-light)"/>
          <stop offset="1" stop-color="var(--navy-deep)"/>
        </linearGradient>
      </defs>
      <path d="M0,188 C90,80 200,48 320,62 C520,92 790,300 1000,384 L1000,0 L0,0 Z" fill="var(--orange-deep)"/>
      <path d="M0,176 C90,70 200,38 320,52 C520,82 790,288 1000,370 L1000,0 L0,0 Z" fill="var(--orange)"/>
      <path d="M0,160 C90,56 200,24 320,38 C520,68 790,272 1000,352 L1000,0 L0,0 Z" fill="url(#bandBlue)"/>
    </svg>

    <div class="holder-name">Dennis Morvale</div>

    <div class="brand-name">
      <span class="brand-mark"></span>
      <span class="brand-text">
        <span class="primary">Quorv</span>
        <span class="secondary">International</span>
      </span>
    </div>

    <ul class="contact-list">
      <li>
        <svg class="contact-icon" viewBox="0 0 24 24"><path d="M6.6 10.8a15 15 0 0 0 6.6 6.6l2.2-2.2c.3-.3.7-.4 1-.2 1.1.4 2.3.6 3.6.6.6 0 1 .4 1 1V20c0 .6-.4 1-1 1A17 17 0 0 1 3 4c0-.6.4-1 1-1h3.5c.6 0 1 .4 1 1 0 1.3.2 2.5.6 3.6.1.3 0 .7-.2 1z"/></svg>
        <span>+61 487215963</span>
      </li>
      <li>
        <svg class="contact-icon" viewBox="0 0 24 24"><path d="M2 5h20v2l-10 6L2 7z M2 9l10 6 10-6v10H2z"/></svg>
        <span>dennis@quorv.com.au</span>
      </li>
      <li>
        <svg class="contact-icon" viewBox="0 0 24 24"><circle cx="12" cy="12" r="10"/></svg>
        <span>www.quorv.com.au</span>
      </li>
    </ul>

    <address class="postal-address">
      P.O. Box 872<br>
      Fernlow QLD 4309
    </address>
  </div>
</body>
</html>
```